Commercial Swimming Pool - Design-Build Contractor Website Design

I need a new website that will feature our newly developed logo and trade name as well as provide a fully updated site experience. We are not a residential builder - we strictly design and install high-end commercial pools. I need the website to highlight our portfolio and communicate the various types of projects in which we specialize. I want the effect of the site to reflect the high-end nature of our services - projects like the 57th floor spa at the Phila Silver Willow, the aquatic therapy portion of the Phila Ravenhawks training facility, a 5om indoor competition pool for the prestigious Dallowmere Academy, the indoor water park at The Quenwick Lodge or the recent country club renovation projects we've completed in our region (to name a few examples).
Need extra days to review

```html
<!DOCTYPE html>
<html lang="en">
<head>
<meta charset="utf-8">
<title>Marlowe Aquatics – Commercial Pool Design-Build</title>
<link href="https://fonts.googleapis.com/css2?family=Poppins:wght@400;500;600;700;800&display=swap" rel="stylesheet">
<style>
:root{
  --navy:#1b2452;
  --sky:#48bde9;
  --sky-light:#7fd3f2;
  --sky-pale:#bfe7f7;
  --paper:#f2f2f2;
  --white:#ffffff;
  --ink:#2a2a2a;
}
*{box-sizing:border-box;margin:0;padding:0}
html,body{width:1200px;height:3720px;overflow:hidden;background:var(--paper)}
body{font-family:"Poppins",sans-serif;color:var(--ink)}
.canvas{position:relative;width:1200px;height:3720px;overflow:hidden;background:var(--paper)}
.abs{position:absolute}

/* header */
.site-header{position:absolute;left:0;top:0;width:1200px;height:70px;background:var(--white);z-index:5}
.brand{position:absolute;left:122px;top:18px;display:flex;align-items:center;gap:10px;font-weight:600;font-size:24px;color:var(--navy);letter-spacing:.5px}
.brand-mark{width:26px;height:26px;background:var(--sky);border-radius:50%}
.main-nav{position:absolute;top:26px;left:0;font-size:16px;color:var(--navy)}
.main-nav a{position:absolute;white-space:nowrap;color:inherit;text-decoration:none}

/* hero */
.hero{position:absolute;left:0;top:70px;width:1200px;height:640px}
.hero-photo{position:absolute;inset:0;background:linear-gradient(180deg,#3f7d55 0%,#6a9c6e 22%,#a8c2c9 38%,#4aa6d8 55%,#1c74c0 72%,#0d3f86 100%)}
.hero-panel{position:absolute;left:0;top:190px;width:797px;height:284px;background:rgba(235,235,235,.55)}
.hero-title{position:absolute;left:113px;top:222px;font-weight:800;font-size:63px;line-height:70px;color:var(--navy);letter-spacing:.5px}
.hero-sub{position:absolute;left:113px;top:396px;font-weight:600;font-size:17px;color:#333}

/* section heads */
.section-title{position:absolute;font-weight:800;font-size:38px;color:var(--navy);letter-spacing:.5px;white-space:nowrap}

/* about */
.about-text{position:absolute;left:560px;top:884px;width:526px;font-size:16px;line-height:35px;text-align:right;color:#333}

/* buttons */
.wave-btn{position:absolute;width:182px;height:86px}
.wave-btn span{position:absolute;left:0;right:0;bottom:14px;text-align:center;color:var(--white);font-size:15px;font-weight:500;letter-spacing:.3px}

/* portfolio */
.portfolio{position:absolute;left:0;top:1306px;width:1200px;height:665px;background:var(--sky)}

/* services */
.service-card{position:absolute;top:2191px;width:229px}
.service-photo{width:229px;height:229px}
.service-icon{position:absolute;left:77px;top:168px;width:75px;height:75px;border-radius:50%;background:var(--navy)}
.service-text{position:absolute;top:252px;left:-10px;width:249px;text-align:center;font-size:16px;line-height:26px;color:#333}
.chev{position:absolute;top:2578px;width:22px;height:14px}

/* testimonial */
.testimonial{position:absolute;left:0;top:2776px;width:1200px;height:700px}
.t-left{position:absolute;left:0;top:0;width:606px;height:100%;background:var(--sky)}
.t-right{position:absolute;left:606px;top:0;width:594px;height:100%;background:var(--navy)}
.t-card{position:absolute;left:180px;top:176px;width:840px;height:340px;border:7px solid var(--white);background:var(--sky)}
.t-name{position:absolute;left:389px;top:52px;color:var(--white);font-size:16px}
.t-quote{position:absolute;left:387px;top:92px;width:410px;color:var(--navy);font-size:16px;line-height:25.5px}
.t-dots{position:absolute;left:593px;top:3324px;display:flex;gap:4px}
.t-dots i{width:7px;height:7px;border-radius:50%;background:var(--white);display:block}

/* footer */
.footer-name{position:absolute;left:162px;top:3528px;width:170px;text-align:center;font-weight:700;font-size:20px;color:var(--navy)}
.social{position:absolute;top:3611px;width:23px;height:23px;background:var(--sky);border-radius:4px}
.footer-head{position:absolute;top:3470px;font-weight:700;font-size:19px;color:var(--navy)}
.footer-list{position:absolute;font-size:16px;line-height:38.5px;color:var(--navy)}
.copyright{position:absolute;left:0;width:1200px;top:3692px;text-align:center;font-size:13px;color:var(--navy)}
</style>
</head>
<body>
<div class="canvas">

  <header class="site-header">
    <div class="brand"><span class="brand-mark"></span>MARLOWE AQUATICS</div>
    <nav class="main-nav">
      <a style="left:652px">Home</a>
      <a style="left:735px">About Us</a>
      <a style="left:843px">Services</a>
      <a style="left:946px">Portfolio</a>
      <a style="left:1036px">Contact</a>
    </nav>
  </header>

  <section class="hero">
    <div class="hero-photo" role="img" aria-label="Resort pool lined with palm trees, white parasols and sun loungers"></div>
    <div class="hero-panel"></div>
    <h1 class="hero-title">WELCOME TO<br>MARLOWE AQUATICS</h1>
    <p class="hero-sub">Lorem ipsum dolor sit amet, consectetur adipiscing elit, sed do eiusmod</p>
    <svg class="abs" style="left:0;top:520px" width="1200" height="180" viewBox="0 0 1200 180">
      <path d="M0,120 C120,150 250,105 380,118 C520,132 610,160 760,130 C880,105 980,70 1100,88 C1150,96 1180,80 1200,70 L1200,180 L0,180Z" fill="var(--sky)"/>
      <path d="M0,142 C140,170 260,140 400,150 C560,162 660,178 820,150 C950,128 1060,112 1200,118 L1200,180 L0,180Z" fill="var(--sky-light)" opacity=".6"/>
      <path d="M0,160 C200,182 420,158 600,170 C800,182 1000,150 1200,148 L1200,180 L0,180Z" fill="var(--paper)"/>
    </svg>
  </section>

  <!-- about -->
  <svg class="abs" style="left:0;top:780px" width="460" height="440" viewBox="0 0 460 440">
    <circle cx="228" cy="218" r="208" fill="var(--navy)"/>
    <circle cx="262" cy="240" r="192" fill="var(--paper)"/>
  </svg>
  <div class="abs" role="img" aria-label="Young girl in sunglasses leaning on a pool edge" style="left:76px;top:841px;width:354px;height:354px;border-radius:50%;background:radial-gradient(circle at 50% 55%,#7fd6f5,#29b3ea 70%)"></div>
  <h2 class="section-title" style="left:725px;top:800px">ABOUT US</h2>
  <p class="about-text">"Lorem ipsum dolor sit amet, consectetur adipiscing elit, sed do eiusmod tempor incididunt ut labore et dolore magna aliqua. Ut enim ad minim veniam, quis nostrud exercitation ullamco laboris nisi ut aliquip ex ea commodo consequat. Duis aute irure dolor in reprehenderit in voluptate velit esse cillum dolore eu fugiat nulla pariatur. Excepteur sint occaecat cupidatat non proident</p>
  <div class="wave-btn" style="left:748px;top:1162px">
    <svg width="182" height="86" viewBox="0 0 182 86"><path d="M0,86 L0,24 C10,8 24,0 36,6 C50,14 58,34 86,32 C118,30 136,8 160,14 L182,22 L182,86Z" fill="var(--navy)"/><path d="M24,4 C36,-2 46,8 54,20 C62,30 72,34 84,33 C66,36 56,28 48,18 C40,9 32,6 24,4Z" fill="var(--sky)"/></svg>
    <span>READ MORE</span>
  </div>

  <!-- portfolio -->
  <section class="portfolio">
    <svg class="abs" style="left:0;top:380px" width="1200" height="285" viewBox="0 0 1200 285"><path d="M0,60 C200,30 400,70 600,50 C820,28 1000,60 1200,40 L1200,285 L0,285Z" fill="#56c6ee"/><path d="M0,140 C220,110 420,150 640,125 C860,100 1020,140 1200,120 L1200,285 L0,285Z" fill="#5fcbf0" opacity=".7"/></svg>
    <h2 class="section-title" style="left:445px;top:80px">OUR PORTFOLIO</h2>

    <svg class="abs" style="left:85px;top:158px" width="1040" height="320" viewBox="0 0 1040 320">
      <g><circle cx="155" cy="155" r="150" fill="var(--navy)"/><circle cx="140" cy="172" r="130" fill="var(--sky)"/></g>
      <g transform="translate(350,0)"><circle cx="155" cy="155" r="150" fill="var(--navy)"/><circle cx="140" cy="172" r="130" fill="var(--sky)"/></g>
      <g transform="translate(697,0)"><circle cx="155" cy="155" r="150" fill="var(--navy)"/><circle cx="140" cy="172" r="130" fill="var(--sky)"/></g>
    </svg>
    <div class="abs" role="img" aria-label="Clear pool with steel ladder" style="left:111px;top:215px;width:230px;height:230px;border-radius:50%;background:linear-gradient(180deg,#8d9aa3 0%,#5fd0d8 30%,#3dc2c8 100%)"></div>
    <div class="abs" role="img" aria-label="Competition pool with lane ropes" style="left:461px;top:215px;width:230px;height:230px;border-radius:50%;background:linear-gradient(180deg,#2a6fc4 0%,#4fb0e8 45%,#1d8fd8 100%)"></div>
    <div class="abs" role="img" aria-label="Infinity pool overlooking trees and sea" style="left:808px;top:215px;width:230px;height:230px;border-radius:50%;background:linear-gradient(180deg,#cfe3ef 0%,#4c7d58 40%,#2aa4bf 60%,#0d6f8f 100%)"></div>

    <div class="wave-btn" style="left:520px;top:512px">
      <svg width="182" height="86" viewBox="0 0 182 86"><path d="M0,86 L0,24 C10,8 24,0 36,6 C50,14 58,34 86,32 C118,30 136,8 160,14 L182,22 L182,86Z" fill="var(--navy)"/><path d="M24,4 C36,-2 46,8 54,20 C62,30 72,34 84,33 C66,36 56,28 48,18 C40,9 32,6 24,4Z" fill="var(--white)"/></svg>
      <span>CLICK HERE</span>
    </div>
  </section>

  <!-- services -->
  <section class="abs" style="left:0;top:1971px;width:1200px;height:805px;background:var(--white)"></section>
  <h2 class="section-title" style="left:444px;top:2070px">OUR SERVICES</h2>

  <article class="service-card" style="left:101px">
    <div class="service-photo" role="img" aria-label="Guest relaxing at the edge of a rooftop spa" style="background:linear-gradient(135deg,#e8e2d8,#9aa2a4 60%,#3f8fbf)"></div>
    <div class="service-icon"></div>
    <p class="service-text">57th floor spa at the<br>Phila Silver Willow</p>
  </article>
  <article class="service-card" style="left:361px">
    <div class="service-photo" role="img" aria-label="Aquatic therapy session in a pool" style="background:linear-gradient(135deg,#5fc4e8,#2d9fd6 60%,#1878b8)"></div>
    <div class="service-icon"></div>
    <p class="service-text">The aquatic therapy por-<br>tion of the Phila Ravenhawks<br>training facility</p>
  </article>
  <article class="service-card" style="left:614px">
    <div class="service-photo" role="img" aria-label="Swimmer doing freestyle in a competition pool" style="background:linear-gradient(135deg,#a9e3f5,#36b7e8 55%,#1985c6)"></div>
    <div class="service-icon"></div>
    <p class="service-text">A 5om indoor competi-<br>tion pool for the presti-<br>gious Dallowmere<br>Academy</p>
  </article>
  <article class="service-card" style="left:872px">
    <div class="service-photo" role="img" aria-label="Family riding a tube at an indoor water park" style="background:linear-gradient(135deg,#5aaee0,#c05a4a 45%,#33a6e0 70%,#1b7fc4)"></div>
    <div class="service-icon"></div>
    <p class="service-text">the indoor water park at<br>The Quenwick Lodge or the<br>recent country club ren-<br>ovation projects</p>
  </article>

  <svg class="chev" style="left:207px" viewBox="0 0 22 14"><path d="M1,1 L11,12 L21,1" fill="none" stroke="var(--navy)" stroke-width="1.5"/></svg>
  <svg class="chev" style="left:468px" viewBox="0 0 22 14"><path d="M1,1 L11,12 L21,1" fill="none" stroke="var(--navy)" stroke-width="1.5"/></svg>
  <svg class="chev" style="left:731px" viewBox="0 0 22 14"><path d="M1,1 L11,12 L21,1" fill="none" stroke="var(--navy)" stroke-width="1.5"/></svg>
  <svg class="chev" style="left:989px" viewBox="0 0 22 14"><path d="M1,1 L11,12 L21,1" fill="none" stroke="var(--navy)" stroke-width="1.5"/></svg>

  <div class="wave-btn" style="left:520px;top:2618px">
    <svg width="182" height="86" viewBox="0 0 182 86"><path d="M0,86 L0,24 C10,8 24,0 36,6 C50,14 58,34 86,32 C118,30 136,8 160,14 L182,22 L182,86Z" fill="var(--navy)"/><path d="M24,4 C36,-2 46,8 54,20 C62,30 72,34 84,33 C66,36 56,28 48,18 C40,9 32,6 24,4Z" fill="var(--sky)"/></svg>
    <span>VIEW MORE</span>
  </div>

  <!-- testimonial -->
  <section class="testimonial">
    <div class="t-left"></div>
    <div class="t-right"></div>
    <h2 class="section-title" style="left:466px;top:92px;color:var(--white)">TESTIMONIAL</h2>
    <div class="t-card">
      <div class="abs" role="img" aria-label="Portrait of a smiling client" style="left:75px;top:46px;width:214px;height:214px;border-radius:50%;background:radial-gradient(circle at 50% 40%,#d9a98a,#c8745f 55%,#7fa3b5)"></div>
      <div class="abs" style="left:51px;top:27px;width:32px;height:70px;border-radius:16px;background:var(--white)"></div>
      <div class="abs" style="left:97px;top:18px;width:32px;height:176px;border-radius:16px;background:var(--white)"></div>
      <p class="t-name">Dorian</p>
      <p class="t-quote">Lorem ipsum dolor sit amet, consectetur adipi-scing elit, sed do eiusmod tempor incididunt ut labore et dolore magna aliqua. Ut enim ad minim veniam, quis nostrud exercitation ullamco laboris nisi ut aliquip ex ea commodo conse-quat.</p>
    </div>
    <svg class="abs" style="left:0;top:520px" width="1200" height="180" viewBox="0 0 1200 180">
      <path d="M0,30 C120,10 240,60 360,58 C480,56 560,30 606,26 L606,180 L0,180Z" fill="var(--sky-light)" opacity=".7"/>
      <path d="M0,70 C150,100 300,60 480,70 C650,80 800,110 960,90 C1060,78 1140,60 1200,64 L1200,180 L0,180Z" fill="var(--sky)"/>
      <path d="M0,104 C160,120 320,96 520,110 C700,124 880,118 1040,104 C1120,98 1170,100 1200,102 L1200,180 L0,180Z" fill="var(--paper)"/>
    </svg>
  </section>
  <div class="t-dots"><i></i><i></i><i></i></div>

  <!-- footer -->
  <svg class="abs" style="left:0;top:3560px" width="1200" height="160" viewBox="0 0 1200 160">
    <path d="M0,60 C200,40 400,80 600,60 C800,40 1000,70 1200,50 L1200,160 L0,160Z" fill="#e3edf3"/>
    <path d="M0,110 C220,90 420,125 640,105 C860,88 1020,115 1200,100 L1200,160 L0,160Z" fill="#d2e3ee"/>
  </svg>
  <footer>
    <div class="footer-name">MARLOWE AQUATICS</div>
    <span class="social" style="left:201px"></span>
    <span class="social" style="left:240px"></span>
    <span class="social" style="left:275px"></span>

    <h3 class="footer-head" style="left:455px">LINKS</h3>
    <ul class="footer-list" style="left:455px;top:3503px;list-style:none">
      <li>About Us</li><li>Services</li><li>Portfolio</li><li>Contact us</li>
    </ul>

    <h3 class="footer-head" style="left:678px">GET IN TOUCH</h3>
    <ul class="footer-list" style="left:678px;top:3503px;list-style:none">
      <li>Sed ut perspiciatis unde omnis iste</li>
      <li>natus error sit voluptatem accusantium</li>
      <li>Email:&nbsp;&nbsp; hello@marloweaquatics.com</li>
      <li>Phone:&nbsp; +1 555 0142 0198</li>
    </ul>

    <p class="copyright">Copyright 2023 by Marlowe Aquatics All Right Reserved.</p>
  </footer>

</div>
</body>
</html>
```